Business Card Makeover. Recreate a sleek modern design for our business card.

DO NOT COPY OUR CURRENT DESIGN. MUST BE ONE SIDED BUSINESS CARD.
Create a new business card design, using our new logo. Attached is a sample of our current design and new logo. Please note the address and email will change. The new address is 412 Corvell West Palm Beach 33401 and our website will be www.delmarhollis.example.

We are an architectural and interior design firm. We prefer a clean modern look. Something that is refined and emulates excellence.

Industry/Entity Type

Architecture

Contact Information for Business Card

clean modern look, please do not copy our attached design.

Font styles to use
Other font styles liked:
• see attached business card font

Colors

Designer to choose colors to be used in the design.

Requirements
Must have
• Must have a modern appeal and resemble our current branding.
Nice to have
• modern font, our logo, legible name and titles progressive design
Should not have
• Do not add colors not reflected in our branding. Should not look like our current card.

```html
<!DOCTYPE html>
<html lang="en">
<head>
<meta charset="utf-8">
<title>Delmar Hollis — Business Card</title>
<link href="https://fonts.googleapis.com/css2?family=Fira+Sans:wght@400&family=PT+Serif:wght@700&display=swap" rel="stylesheet">
<style>
  :root {
    --brand-blue: #0a4fb5;
    --ink-dark: #454545;
    --ink-grey: #7b7b7b;
    --logo-grey: #6f6f6f;
    --card-white: #ffffff;
    --backdrop: #e8e8e6;
  }
  * { margin: 0; padding: 0; box-sizing: border-box; }
  html, body {
    width: 1125px;
    height: 1200px;
    overflow: hidden;
    background: var(--backdrop);
  }
  .canvas {
    position: relative;
    width: 1125px;
    height: 1200px;
  }
  .card {
    position: absolute;
    left: 62px;
    top: 315px;
    width: 1000px;
    height: 569px;
    background: var(--card-white);
    box-shadow: 0 6px 18px rgba(0,0,0,0.18);
    font-family: "Fira Sans", sans-serif;
  }
  .person-name {
    position: absolute;
    left: 46px;
    top: 78px;
    font-family: "PT Serif", serif;
    font-weight: 700;
    font-size: 38px;
    line-height: 1;
    color: var(--brand-blue);
  }
  .person-title {
    position: absolute;
    left: 46px;
    top: 128px;
    font-size: 22px;
    letter-spacing: 0.4px;
    color: var(--ink-dark);
  }
  .title-rule {
    position: absolute;
    left: 46px;
    top: 168px;
    width: 292px;
    height: 2px;
    background: var(--brand-blue);
  }
  .license {
    position: absolute;
    left: 46px;
    top: 283px;
    font-size: 22px;
    color: var(--ink-dark);
  }
  .address {
    position: absolute;
    left: 46px;
    top: 315px;
    width: 260px;
    font-size: 22px;
    line-height: 29px;
    letter-spacing: 0.3px;
    color: var(--ink-grey);
  }
  .contact-list {
    position: absolute;
    left: 46px;
    top: 380px;
    list-style: none;
  }
  .contact-item {
    display: flex;
    align-items: center;
    height: 31px;
    font-size: 22px;
    color: var(--ink-grey);
  }
  .contact-item svg {
    width: 15px;
    height: 15px;
    margin-right: 11px;
    fill: var(--brand-blue);
    flex: none;
  }
  .wordmark {
    position: absolute;
    left: 506px;
    top: 239px;
    display: flex;
    align-items: center;
  }
  .wordmark-dot {
    width: 90px;
    height: 90px;
    border-radius: 50%;
    background: var(--brand-blue);
    margin-right: 18px;
  }
  .wordmark-name {
    font-size: 36px;
    font-weight: 400;
    letter-spacing: 1px;
    color: var(--logo-grey);
    text-transform: uppercase;
  }
</style>
</head>
<body>
<main class="canvas">
  <section class="card">
    <h1 class="person-name">Owen Whitcombe</h1>
    <p class="person-title">Partner / Director of Design</p>
    <div class="title-rule"></div>

    <p class="license">LIC.# AA26004715</p>
    <p class="address">412 Corvell West Palm Beach 33401</p>

    <ul class="contact-list">
      <li class="contact-item">
        <svg viewBox="0 0 16 16" aria-hidden="true"><path d="M3.5 1.5l2.5 0 1 3.5-1.8 1.2a9 9 0 0 0 4.6 4.6L11 9l3.5 1v2.5c0 1-1 2-2 2A11 11 0 0 1 1.5 3.5c0-1 1-2 2-2z"/></svg>
        561.555.0142
      </li>
      <li class="contact-item">
        <svg viewBox="0 0 16 16" aria-hidden="true"><rect x="4" y="1" width="8" height="4"/><path d="M1 6h14v6h-3v-2H4v2H1z"/><rect x="5" y="11" width="6" height="4"/></svg>
        561.555.0187
      </li>
      <li class="contact-item">
        <svg viewBox="0 0 16 16" aria-hidden="true"><path d="M4 0h8a1 1 0 0 1 1 1v14a1 1 0 0 1-1 1H4a1 1 0 0 1-1-1V1a1 1 0 0 1 1-1zm1 2v10h6V2zm3 11a1 1 0 1 0 0 2 1 1 0 0 0 0-2z"/></svg>
        561.555.0163
      </li>
      <li class="contact-item">
        <svg viewBox="0 0 16 16" aria-hidden="true"><path d="M0 3h16v10H0zm2 2v6h12V5l-6 4z"/></svg>
        owen@delmarhollis.example
      </li>
      <li class="contact-item">
        <svg viewBox="0 0 16 16" aria-hidden="true"><circle cx="8" cy="8" r="7.5"/><path d="M4 4c2 0 3 2 2 4s1 3 0 5M10 2c-1 2 1 3 3 3M12 10c-1 0-2 1-1 3" stroke="#fff" stroke-width="1.3" fill="none"/></svg>
        www.delmarhollis.example
      </li>
    </ul>

    <div class="wordmark">
      <div class="wordmark-dot"></div>
      <span class="wordmark-name">Delmar Hollis</span>
    </div>
  </section>
</main>
</body>
</html>
```